Business Card Design for company

We want new business cards. We'd like something different-- yet still highly professional. Our tagline is Providing leadership, delivering success. Stock photos are ok, as long as they are relevant and look upscale.

Target Market(s)

Architecture/Business Management Consulting/Engineering Consulting

Contact Information for Business Card

dark gray background with pops of blue might be good, but you tell me. You're the designers. Rounded corners might be nice, but again, you tell me.

Font styles to use
Serif
Sans Serif

Colors
3276b5
5c5c5c
9d9d9d
fbfbfb

Requirements
Nice to have
• Something different, but still very professional.

```html
<!DOCTYPE html>
<html lang="en">
<head>
<meta charset="utf-8">
<title>Norvale Partners – Business Cards</title>
<link rel="stylesheet" href="https://fonts.googleapis.com/css2?family=Montserrat:wght@400;500&family=Open+Sans:wght@400;600&display=swap">
<style>
  :root {
    --blue: #3276b5;
    --blue-deep: #2a64a0;
    --gray-dark: #5c5c5c;
    --gray-mid: #9d9d9d;
    --card: #fbfbfb;
    --stage: #2b2b2b;
    --text: #333333;
  }
  * { margin: 0; padding: 0; box-sizing: border-box; }
  html, body { width: 1200px; height: 930px; overflow: hidden; }
  body { background: var(--stage); font-family: "Open Sans", Arial, sans-serif; position: relative; }

  .card {
    position: absolute;
    width: 600px; height: 343px;
    background: var(--card);
    border-radius: 16px;
    overflow: hidden;
  }
  .card--front { left: 80px; top: 70px; }
  .card--back  { left: 520px; top: 517px; background: #ffffff; }

  /* Front */
  .world-map {
    position: absolute; left: 50px; top: 20px; width: 500px; height: 300px;
    background: radial-gradient(ellipse at center, #e4e4e4 0%, #eeeeee 55%, rgba(251,251,251,0) 75%);
  }
  .brand {
    position: absolute; left: 0; right: 0; top: 96px; text-align: center;
  }
  .brand-name {
    font-family: "Montserrat", Arial, sans-serif; font-weight: 500;
    font-size: 50px; letter-spacing: 4px; color: var(--gray-dark);
    line-height: 1; white-space: nowrap;
  }
  .brand-name::before {
    content: ""; display: inline-block; width: 18px; height: 18px;
    background: var(--blue); margin-right: 16px; vertical-align: middle;
    position: relative; top: -4px;
  }
  .brand-sub {
    margin-top: 8px;
    font-family: "Montserrat", Arial, sans-serif; font-weight: 500;
    font-size: 24px; letter-spacing: 6px; color: var(--gray-dark);
    line-height: 1;
  }
  .tagline {
    margin-top: 26px;
    font-family: "Montserrat", Arial, sans-serif; font-size: 13px;
    letter-spacing: 2.4px; color: var(--gray-dark); text-transform: uppercase;
  }

  /* Back */
  .wave { position: absolute; left: 0; bottom: 0; width: 600px; height: 140px; }
  .person { position: absolute; left: 18px; top: 140px; width: 302px; text-align: right; }
  .person-name {
    font-family: "Open Sans", Arial, sans-serif; font-weight: 400;
    font-size: 27px; color: var(--blue); letter-spacing: 0.3px; line-height: 1.1;
    white-space: nowrap;
  }
  .person-role { font-size: 18px; color: var(--text); margin-top: 4px; white-space: nowrap; }
  .divider {
    position: absolute; left: 338px; top: 48px; width: 1.5px; height: 170px; background: var(--blue);
  }
  .contact { position: absolute; left: 356px; top: 44px; list-style: none; font-size: 12.5px; color: var(--text); line-height: 1.35; }
  .contact li { display: flex; align-items: flex-start; gap: 7px; margin-bottom: 5px; white-space: nowrap; }
  .contact .icon { width: 12px; height: 12px; flex: none; margin-top: 2px; }
</style>
</head>
<body>

<section class="card card--front" aria-label="Card front">
  <div class="world-map" role="img" aria-label="Faint dotted world map in light gray"></div>
  <div class="brand">
    <div class="brand-name">NORVALE</div>
    <div class="brand-sub">PARTNERS</div>
    <div class="tagline">Clear Thinking | Lasting Results</div>
  </div>
</section>

<section class="card card--back" aria-label="Card back">
  <div class="person">
    <div class="person-name">DANIEL HARGREAVE</div>
    <div class="person-role">Design Consultant</div>
  </div>
  <div class="divider"></div>
  <ul class="contact">
    <li><svg class="icon" viewBox="0 0 12 12"><path d="M2 1l2 0 1 3-1.5 1a6 6 0 0 0 3 3L8 7l3 1v2c0 1-1 1.5-2 1.5A9 9 0 0 1 .5 3C.5 2 1 1 2 1z" fill="var(--blue)"/></svg><span>01632 960412 (Ashbury)<br>01632 960587 (Kelmford)<br>555-014-2290</span></li>
    <li><svg class="icon" viewBox="0 0 12 12"><rect x="1" y="2.5" width="10" height="7" fill="none" stroke="var(--blue)" stroke-width="1.2"/><path d="M1 2.5l5 4 5-4" fill="none" stroke="var(--blue)" stroke-width="1.2"/></svg><span>hello@norvalepartners</span></li>
    <li><svg class="icon" viewBox="0 0 12 12"><path d="M1 7l10-4-4 8-1.5-3z" fill="none" stroke="var(--blue)" stroke-width="1.1"/></svg><span>Unit 8, The Linford Centre,<br>Mill Lane, Ashbury,<br>Herts AB1 2CD</span></li>
    <li><svg class="icon" viewBox="0 0 12 12"><circle cx="6" cy="6" r="5" fill="none" stroke="var(--blue)" stroke-width="1.1"/><path d="M1 6h10M6 1c-3 3-3 7 0 10M6 1c3 3 3 7 0 10" fill="none" stroke="var(--blue)" stroke-width="0.9"/></svg><span>norvalepartners.com</span></li>
  </ul>
  <svg class="wave" viewBox="0 0 600 140" preserveAspectRatio="none" aria-hidden="true">
    <path d="M0 140 L0 108 C140 60 300 112 600 20 L600 140 Z" fill="var(--gray-mid)"/>
    <path d="M0 140 L0 122 C150 78 320 120 600 38 L600 140 Z" fill="#ffffff"/>
    <path d="M0 140 L0 128 C160 92 330 128 600 46 L600 140 Z" fill="var(--blue-deep)"/>
  </svg>
</section>

</body>
</html>
```